Business Card Design

My business is writing crime novels to entertain readers. I write legal thrillers and mysteries. I need a card for publishers, agents, other authors, and media.

Industry/Entity Type

Legal

Contact Information for Business Card

Paul Derrow
www.derrowfiction.example
pauljderrow@inkpost.example
0064 27 5190472

```html
<!DOCTYPE html>
<html lang="en">
<head>
<meta charset="utf-8">
<title>Paul Derrow — Business Card</title>
<link rel="stylesheet" href="https://fonts.googleapis.com/css2?family=Tinos:wght@400&display=swap">
<style>
  :root {
    --card-bg: #dddcda;
    --ink: #121212;
    --arc-black: #050505;
    --arc-deep: #0d0d0d;
    --arc-mid: #3a3a3a;
    --arc-light: #8c8c8c;
    --portrait-dark: #1c1c1c;
    --portrait-mid: #5a5a5a;
    --portrait-light: #b9b9b9;
  }
  * { margin: 0; padding: 0; box-sizing: border-box; }
  html, body {
    width: 1200px;
    height: 741px;
    overflow: hidden;
    background: var(--card-bg);
  }
  .business-card {
    position: relative;
    width: 1200px;
    height: 741px;
    background: var(--card-bg);
    overflow: hidden;
  }
  .feature-arc {
    position: absolute;
    inset: 0;
    width: 1200px;
    height: 741px;
  }
  .author-details {
    position: absolute;
    left: 94px;
    top: 292px;
    width: 500px;
    text-align: center;
    color: var(--ink);
    font-family: "Tinos", "Times New Roman", serif;
  }
  .author-name {
    font-size: 50px;
    font-weight: 400;
    font-variant: small-caps;
    letter-spacing: 4px;
    line-height: 1;
    margin-bottom: 14px;
  }
  .contact-line {
    font-size: 28px;
    line-height: 38px;
    letter-spacing: 0.3px;
  }
</style>
</head>
<body>
  <main class="business-card">
    <svg class="feature-arc" viewBox="0 0 1200 741" xmlns="http://www.w3.org/2000/svg">
      <defs>
        <linearGradient id="arcFill" x1="0" y1="1" x2="1" y2="0">
          <stop offset="0" stop-color="var(--arc-deep)"/>
          <stop offset="0.45" stop-color="var(--arc-mid)"/>
          <stop offset="1" stop-color="var(--arc-light)"/>
        </linearGradient>
        <linearGradient id="portraitFill" x1="0" y1="0" x2="0" y2="1">
          <stop offset="0" stop-color="var(--portrait-light)"/>
          <stop offset="0.45" stop-color="var(--portrait-mid)"/>
          <stop offset="1" stop-color="var(--portrait-dark)"/>
        </linearGradient>
      </defs>
      <path class="arc-outer" d="M886 0 C 700 110, 566 400, 573 741 L 1200 741 L 1200 0 Z" fill="var(--arc-black)"/>
      <path class="arc-inner" d="M968 0 C 800 130, 660 420, 668 741 L 1200 741 L 1200 0 Z" fill="url(#arcFill)"/>
      <path class="arc-edge" d="M968 0 C 800 130, 660 420, 668 741" fill="none" stroke="#2a2a2a" stroke-width="3"/>
      <path class="author-portrait" role="img" aria-label="Portrait photograph of the author in glasses, white shirt and black leather jacket"
            d="M870 150 C 870 90, 1070 90, 1075 150 L 1080 330 C 1150 360, 1185 420, 1190 500 L 1190 741 L 745 741 L 752 520 C 760 420, 820 360, 880 335 Z"
            fill="url(#portraitFill)"/>
    </svg>

    <section class="author-details">
      <h1 class="author-name">Paul Derrow</h1>
      <p class="contact-line website">www.derrowfiction.example</p>
      <p class="contact-line email">pauljderrow@inkpost.example</p>
      <p class="contact-line phone">0064 27 5190472</p>
    </section>
  </main>
</body>
</html>
```